Church Website with Home Page and Member Sermon Library

I am in need of an updated design for our church website. This will include 4 pages (outlined below). We are a conservative, evangelical, Christian church. The site should be modern and clean, while still reflecting our conservative values. I already have a logo for our church, and I want the site to incorporate the logo, and match the logo/branding. Stock photos are allowed if needed, but I have uploaded some images of our church and would prefer those images to be used if possible. Any stock photos used should not include any people in the photos (scenery, nature, buildings, animals, etc. are fine).

The site will need 4 pages: Home, Support Us (Donate), Login, and Recording Library.

Page 1: Home
The home page should include the following sections:

- Navigation: Should include links to each section of the home page plus a "listen live" link which will take the user to a live-streaming site and a "support us" link which will take the user to a support/donate page.

- Announcements: Can be either a banner or some other design, but there needs to be some way for us to post announcements for visitors to see. I'm open for creative ideas in this section, but would like it not to take up a lot of room on the page.

- About Us: Should include address, service times (see attached document), and information about the church.

- Pastor Bio: A section that introduces our pastor and gives a short bio about our pastor. Would like this section to include a picture of our pastor. Somewhere in this section I would like to include this Bible reference: "And I will give you pastors according to mine heart, which shall feed you with knowledge and understanding. Jer 3:15 LPW"

- Articles of Faith (What We Believe): This should include several sub-sections each with a heading, body, and possibly 1 or more scripture references. I have attached a document to the brief that includes our articles of faith. Feel free to be creative with this section in how you lay these out and format them.

- Support Us: A small section that explains what kind of support someone can give and a link to a donation page. The link can say something like "Support Us" or "Donate Now".

- Contact form: A contact form that allows the visitor to send us a message. The contact form should ask for name, email, phone, and message.

- Footer: A footer that will be displayed on all pages of the site. This should include at a minimum a link to the home page (or a link to each individual section in the home page if you prefer), a link to "listen live", a link to "support us", a link to "contact us" (or you can put the contact form directly in the footer if you prefer), the address, and a "member login" link.

Page 2: Support Us
The donation page should include a form the visitor can fill out to make a donation. We will embed a third party form later. For this design, please just mock out the design with a basic form asking for name, phone, and email.

Page 3: Login
The recording library (detailed below) will require members to login with a shared numeric code before accessing the page. We need a design for a login screen. The screen should include navigation/footer just like all other pages, but the body of the login page will consist only of a form that asks the user to enter the access code and then a "login" button.

Page 4: Recording Library

The library page is a member-only page that will require a shared, numeric pass code to access. On this page, members will be able to access a filterable list of past sermons. The page by default should display most recent sermons, but should also include a search form that allows the member to filter the sermon list to find a particular sermon. The search form should allow the user to select a filter type (e.g. Speaker name, date, event, etc.) and type in a value to search. They should be able to add multiple filters and remove filters that have been added. Each sermon that is displayed in the result list should include basic information such as title, date, speaker, tags, etc. along with a download icon, and an embedded audio player where they can click a play button to stream it on-demand. Each sermon should also have clickable tags associated with it that can be used to find related sermons.
Updates

I have uploaded several images of our church. Feel free to incorporate these into your design if possible.

Target Market(s)

Church Members

Industry/Entity Type

Religion

Number of Pages Required

4 page

Font styles to use
Sans Serif

Colors

Designer to choose colors to be used in the design.

Requirements
Must have
• Must incorporate the logo (attached)
Nice to have
• Would like the design to incorporate pictures of our church (attached) instead of stock photos if possible.
Should not have
• Please avoid an overly cluttered design. Stock photos used should not include any people in the photos.

```html
<!DOCTYPE html>
<html lang="en">
<head>
<meta charset="utf-8">
<title>Cedar Grove Church</title>
<link href="https://fonts.googleapis.com/css2?family=Marcellus&family=Montserrat:wght@400;500;600;700&display=swap" rel="stylesheet">
<style>
:root{
  --green:#7fa866;
  --green-dark:#2f4525;
  --teal:#1fb8d6;
  --teal-soft:#2fc0da;
  --text:#4a4a4a;
  --muted:#777;
  --line:#c9d8bf;
  --paper:#ffffff;
  --mist:#eef1ed;
}
*{box-sizing:border-box;margin:0;padding:0}
html,body{width:1200px;height:4461px;overflow:hidden;background:var(--paper)}
body{position:relative;font-family:'Montserrat',sans-serif;color:var(--text)}
.abs{position:absolute}
.serif{font-family:'Marcellus',serif;font-weight:400}
.brand{font-family:'Marcellus',serif;color:var(--teal);font-size:26px;letter-spacing:3px;display:flex;align-items:center;gap:12px}
.brand-mark{width:22px;height:22px;border:2px solid var(--teal);border-radius:50%}

/* header */
.site-header{top:0;left:0;width:1200px;height:87px;background:#fff}
.nav{top:40px;left:360px;display:flex;font-size:11.5px;text-transform:uppercase;color:#555;white-space:nowrap}
.nav a{color:inherit;text-decoration:none;padding:0 17px;border-right:1px solid #bbb;line-height:14px}
.nav a:first-child{padding-left:0;color:#333;position:relative}
.nav a:first-child::after{content:"";position:absolute;left:0;bottom:-14px;width:62px;height:2px;background:var(--teal)}
.nav a:last-child{border:none;padding-right:0}
.pill{border-radius:20px;color:#fff;font-size:12px;text-transform:uppercase;display:flex;align-items:center;justify-content:center;gap:6px;height:38px;white-space:nowrap}
.pill.live{background:var(--green)}
.pill.support{background:var(--teal)}

/* hero */
.hero{top:87px;left:0;width:1200px;height:583px;background:linear-gradient(180deg,#e8e9e6 0%,#dcdcd8 30%,#b38c70 60%,#a7866c 78%,#cbc6bd 100%)}
.hero-frame{top:158px;left:338px;width:526px;height:162px;border:1.5px solid var(--green)}
.welcome{top:140px;left:507px;width:182px;height:35px;background:var(--teal);color:#fff;font-family:'Marcellus',serif;font-size:20px;letter-spacing:3px;display:flex;align-items:center;justify-content:center}
.hero-title{left:338px;width:526px;text-align:center;font-size:46px;line-height:50px;letter-spacing:2px}
.hero-title .l1{color:var(--green)}
.hero-title .l2{color:#2d2d2d}
.hero-live{top:298px;left:528px;width:172px;height:45px;font-size:15px}

.announce-shadow{top:618px;left:153px;width:929px;height:128px;border:2px solid var(--teal);border-top:none;border-left:none}
.announce{top:608px;left:145px;width:929px;height:128px;background:var(--green);color:#fff;text-align:center;padding-top:40px}
.announce h2{font-size:19px;letter-spacing:2px;font-weight:600}
.announce p{font-size:15px;margin-top:6px}

.dots{background-image:radial-gradient(#b9b9b9 1.3px,transparent 1.5px);background-size:8px 8px}

/* about */
.h-section{font-size:40px;color:var(--green);letter-spacing:1px}
.rule{height:2px;background:var(--teal);width:80px}
.body{font-size:12.5px;line-height:25px;color:#444}
.photo{background:linear-gradient(180deg,#e2e2df 0%,#d8d6d1 35%,#a9876f 60%,#8f7563 72%,#cfcbc4 100%)}
.frame{border:1.5px solid var(--teal)}
.timing{font-size:15px;color:var(--green);font-weight:600;display:flex;align-items:center;gap:10px}
.timing::after{content:"";width:60px;height:1.5px;background:var(--green)}
.times{list-style:none;font-size:12.5px;line-height:28px;color:#444}
.times li::before{content:"";display:inline-block;width:5px;height:5px;background:var(--green);margin-right:10px;vertical-align:middle}

/* pastor */
.pastor-bg{top:1394px;left:0;width:1200px;height:610px;background:linear-gradient(180deg,#e7ece7 0%,#eef1ee 50%,#e4e8e2 100%)}
.quote{top:1753px;left:147px;width:473px;min-height:105px;background:var(--teal);color:#fff;border-radius:0 40px 0 0;padding:20px 36px 16px 40px;font-size:12.5px;line-height:20px}
.quote em{font-style:italic}
.quote b{display:block;margin-top:4px;font-weight:600}
.portrait{background:linear-gradient(160deg,#cfc8bd 0%,#b7a996 40%,#2b2b2d 70%,#1f1f21 100%)}

/* faith */
.faith-h{font-family:'Montserrat',sans-serif;font-size:20px;letter-spacing:3.5px;color:#445a36;text-transform:uppercase;font-weight:500}
.dot{width:13px;height:13px;border-radius:50%;background:var(--green)}
.vline{width:1.5px;background:var(--line)}
.small{font-size:12px;line-height:31px;color:#444}

/* support */
.teal-band{top:3420px;left:0;width:1200px;height:664px;background:linear-gradient(180deg,#2fc0da,#1fb3cf)}
.support-box{top:3060px;left:128px;width:960px;height:461px;background:var(--green)}
.support-img{top:3060px;left:128px;width:480px;height:461px;background:linear-gradient(90deg,#d9d9d6 0%,#cfcfcb 55%,var(--green) 100%)}
.btn-dark{background:var(--green-dark);color:#fff;border-radius:22px;font-size:12.5px;font-weight:700;display:flex;align-items:center;justify-content:center;letter-spacing:.5px}

/* contact */
.field{background:#fff;border-radius:3px;font-size:13.5px;color:#666;display:flex;align-items:center;padding-left:20px;gap:8px}
.field.msg{align-items:flex-start;padding-top:18px}
.send{border:2px solid #fff;border-radius:26px;color:#fff;font-weight:700;font-size:14px;display:flex;align-items:center;justify-content:center;letter-spacing:.5px}

/* footer */
.foot-h{font-size:14px;letter-spacing:2.5px;color:var(--green);text-transform:uppercase}
.foot-col{border-left:1.5px solid var(--line)}
.foot-links{list-style:none;font-size:13px;line-height:30.5px;color:#555}
.foot-btn{border-radius:16px;color:#fff;font-size:11px;display:flex;align-items:center;justify-content:center;text-transform:uppercase}
.copy{top:4408px;left:0;width:1200px;height:53px;background:#eeeeec;font-size:12px;color:#777;display:flex;align-items:center;justify-content:center}
</style>
</head>
<body>

<header class="abs site-header">
  <div class="abs brand" style="top:28px;left:125px"><span class="brand-mark"></span>CEDAR GROVE</div>
  <nav class="abs nav">
    <a href="#about">About Us</a><a href="#pastor">Pastor Bio</a><a href="#faith">Articles of Faith</a><a href="#contact">Contact</a>
  </nav>
  <a class="abs pill live" style="top:28px;left:831px;width:130px">
    <svg width="16" height="16" viewBox="0 0 16 16" fill="none" stroke="#fff" stroke-width="1.5"><circle cx="8" cy="7" r="2"/><path d="M4.5 10.5a5 5 0 1 1 7 0M8 9v6"/></svg>Listen Live</a>
  <a class="abs pill support" style="top:28px;left:966px;width:128px">
    <svg width="16" height="16" viewBox="0 0 16 16" fill="none" stroke="#fff" stroke-width="1.5"><path d="M2 10l4 4h6l2-3M3 9l5-5 3 3"/></svg>Support Us</a>
</header>

<section class="abs hero" role="img" aria-label="Photo of the brick church building under an overcast sky"></section>
<div class="abs hero-frame"></div>
<div class="abs welcome">WELCOME TO</div>
<h1 class="abs hero-title serif" style="top:186px"><span class="l1">CEDAR GROVE</span><br><span class="l2">CHURCH</span></h1>
<a class="abs pill live hero-live">
  <svg width="20" height="20" viewBox="0 0 16 16" fill="none" stroke="#fff" stroke-width="1.4"><circle cx="8" cy="7" r="2"/><path d="M4.5 10.5a5 5 0 1 1 7 0M8 9v6"/></svg>LISTEN LIVE</a>

<div class="abs announce-shadow"></div>
<div class="abs announce"><h2>ANNOUNCEMENT HEADLINE</h2><p>Ut enim ad minim veniam quis nostrud exercitation Allamco laboris nisi ut aliquip ex ea</p></div>
<div class="abs dots" style="top:692px;left:1028px;width:66px;height:62px"></div>

<section id="about">
  <h2 class="abs h-section serif" style="top:835px;left:159px">ABOUT OUR CHURCH</h2>
  <div class="abs rule" style="top:890px;left:159px"></div>
  <p class="abs body" style="top:917px;left:158px;width:410px">Lorem ipsum dolor sit amet, consectetur adipiscing elit, sed do eiusmod tempor incididunt ut labore et dolore magna aliqua. Ut enim ad minim veniam quis nostrud exercitation</p>
  <div class="abs dots" style="top:1014px;left:136px;width:98px;height:92px"></div>
  <div class="abs frame" style="top:1042px;left:162px;width:434px;height:289px"></div>
  <div class="abs photo" style="top:1029px;left:154px;width:433px;height:293px" role="img" aria-label="Photo of the church building and parking lot"></div>

  <p class="abs body" style="top:838px;left:632px;width:450px;line-height:24.5px">Lorem ipsum dolor sit amet, consectetur adipiscing elit, sed do eiusmod tempor incididunt ut labore et dolore magna aliqua. Ut enim ad minim veniam quis nostrud exercitation</p>
  <p class="abs body" style="top:916px;left:632px;width:450px;line-height:24.5px">Allamco laboris nisi ut aliquip ex ea commodo consequat. Duis aute irure dolor in reprehenderit in voluptate velit.Lorem ipsum dolor sit amet, consectetur adipiscing elit, sed do eiusmod tempor incididunt ut labore et dolore magna aliqua. Ut enim ad minim veniam quis nostrud exercitation Allamco laboris nisi ut aliquip ex ea commodo consequat. Duis aute irure dolor in reprehenderit in voluptate velit.</p>
  <div class="abs timing" style="top:1105px;left:635px">SERVICE TIMING:</div>
  <ul class="abs times" style="top:1139px;left:637px">
    <li>WEDNESDAY NIGHT SERVICE: 7:30 PM</li>
    <li>SUNDAY SCHOOL: 10:00 AM</li>
    <li>SUNDAY MORNING SERVICE: 11:00 AM</li>
    <li>SUNDAY NIGHT SERVICE: 5:30 PM</li>
  </ul>
</section>

<section id="pastor">
  <div class="abs pastor-bg" role="img" aria-label="Faded photo of the church grounds"></div>
  <h2 class="abs h-section serif" style="top:1505px;left:152px">OUR PASTOR</h2>
  <div class="abs rule" style="top:1560px;left:152px"></div>
  <p class="abs body" style="top:1590px;left:153px;width:480px;line-height:24px">Lorem ipsum dolor sit amet, consectetur adipiscing elit, sed do eiusmod tempor incididunt ut labore et dolore magna aliqua. Ut enim ad minim veniam quis nostrud exercitation Allamco laboris nisi ut aliquip ex ea commodo consequat. Duis aute irure dolor in reprehenderit in voluptate velit.Lorem ipsum dolor sit amet, consectetur adipiscing elit,</p>
  <div class="abs quote"><em>“And I will give you pastors according to mine heart, which shall feed you with knowledge and understanding”</em><b>Jer 3:15 LPW</b></div>
  <div class="abs" style="top:1494px;left:670px;width:360px;height:380px;border:1.5px solid var(--green);border-bottom:none;border-left:none"></div>
  <div class="abs" style="top:1763px;left:928px;width:120px;height:118px;background:var(--green)"></div>
  <div class="abs portrait" style="top:1508px;left:688px;width:346px;height:361px" role="img" aria-label="Portrait of the pastor holding a Bible"></div>
</section>

<section id="faith">
  <h2 class="abs serif" style="top:2064px;left:0;width:1200px;text-align:center;font-size:40px;color:var(--green);letter-spacing:1px">ARTICLES OF FAITH</h2>
  <div class="abs rule" style="top:2120px;left:560px"></div>

  <div class="abs vline" style="top:2216px;left:121px;height:600px"></div>
  <div class="abs vline" style="top:2216px;left:623px;height:600px"></div>

  <div class="abs dot" style="top:2211px;left:115px"></div>
  <h3 class="abs faith-h" style="top:2213px;left:152px">The God Head.</h3>
  <p class="abs body" style="top:2250px;left:152px;width:430px">We believe in the God head bodily, known as the Divine Trinity. This body consist of God the father, Jesus Christ, his only begotten son and the redeemer of the world, and of the Holy Ghost, The third person of the Divine Trinity.</p>

  <div class="abs dot" style="top:2211px;left:617px"></div>
  <h3 class="abs faith-h" style="top:2213px;left:653px">Baptism of the Holy Ghost</h3>
  <p class="abs body" style="top:2250px;left:653px;width:440px">We believe in the baptism of the Holy Ghost as it is taught in the Bible and promised by our Lord Jesus Christ, with speaking in tongues as the Spirit gives utterance as the initial evidence. Acts 2:4 we believe that the gift of the Holy Ghost is for all believers as the Lord promised. Acts 2:17-1</p>

  <div class="abs dot" style="top:2445px;left:115px"></div>
  <h3 class="abs faith-h" style="top:2435px;left:152px">Full Salvation</h3>
  <p class="abs small" style="top:2468px;left:152px;width:430px;line-height:26px">We believe that Salvation is received only when a person comes to the realization that he or she is lost and separated from God and becomes full of godly sorrow, confessing their sins and true repentance, believing in the shed blood of the Lord Jesus Christ as the only sacrifice for sins. Through the blood of Christ we have:</p>
  <ul class="abs small" style="top:2605px;left:155px;list-style:none">
    <li>(1) remission of sins, Matthew 26:28 Heb 9:22</li>
    <li>(2) Sanctification. Hebrews 13:12</li>
    <li>(3) redemption. Revelations 5:9</li>
    <li>(4) cleansing. 1 John 1:7 Rev. 1:5</li>
    <li>(5). Justification. Romans 5:9</li>
  </ul>

  <div class="abs dot" style="top:2445px;left:617px"></div>
  <h3 class="abs faith-h" style="top:2437px;left:653px">Divine Healing</h3>
  <p class="abs body" style="top:2472px;left:653px;width:440px">We believe Divine Healing to be included in the atonement of Jesus Christ our Lord, And believe that it is still for us today. 1 Peter 2:24 Luke 9:1-2 Mark 16-18 James 5:15</p>

  <div class="abs dot" style="top:2632px;left:617px"></div>
  <h3 class="abs faith-h" style="top:2627px;left:653px">Second Coming of Christ</h3>
  <p class="abs body" style="top:2662px;left:653px;width:430px">We believe in the second coming of Jesus Christ. Matthew 24:44 Luke 12:40</p>

  <div class="abs dot" style="top:2810px;left:115px"></div>
  <h3 class="abs faith-h" style="top:2803px;left:154px">Sanctification</h3>
  <p class="abs body" style="top:2837px;left:154px;width:410px">“Sanctify them through thy truth thy word is truth St John 17:17. For this is the will of God even your sanctification”</p>
  <p class="abs body" style="top:2895px;left:154px;width:410px">We believe in a set apart life, separate from the world to Christ 2 Cor 6:17-18</p>

  <div class="abs dot" style="top:2816px;left:617px"></div>
  <h3 class="abs faith-h" style="top:2809px;left:653px">Eternity</h3>
  <p class="abs body" style="top:2845px;left:653px;width:440px">We believe in Literal Eternity. Eternal Life for the believer and eternal death for those without Christ. Revelations 21:1-27</p>
</section>

<section id="support">
  <div class="abs teal-band" role="img" aria-label="Faded photo of the church building in teal tone"></div>
  <div class="abs dots" style="top:3036px;left:1002px;width:112px;height:108px"></div>
  <div class="abs support-box"></div>
  <div class="abs support-img" role="img" aria-label="Photo of a folded banknote placed in a donation slot"></div>
  <h2 class="abs serif" style="top:3160px;left:632px;font-size:38px;color:#fff;letter-spacing:1px">SUPPORT US</h2>
  <div class="abs" style="top:3214px;left:632px;width:80px;height:2px;background:#fff"></div>
  <p class="abs body" style="top:3240px;left:632px;width:380px;color:#fff;line-height:23.5px;font-size:14px">Lorem ipsum dolor sit amet, consectetur adipiscing elit, sed do eiusmod tempor incididunt ut labore et dolore magna aliqua. Ut enim ad minim veniam, quis nostrud exercitation</p>
  <a class="abs btn-dark" style="top:3360px;left:625px;width:180px;height:42px">DONATE NOW</a>
</section>

<section id="contact">
  <h2 class="abs serif" style="top:3592px;left:0;width:1200px;text-align:center;font-size:38px;color:#fff;letter-spacing:1px">CONTACT US</h2>
  <div class="abs" style="top:3646px;left:560px;width:80px;height:2px;background:#fff"></div>
  <div class="abs field" style="top:3678px;left:201px;width:391px;height:52px">
    <svg width="14" height="14" viewBox="0 0 14 14" fill="#999"><circle cx="7" cy="4" r="3"/><path d="M1 14c0-4 3-6 6-6s6 2 6 6z"/></svg>First Name</div>
  <div class="abs field" style="top:3678px;left:601px;width:390px;height:52px">
    <svg width="14" height="14" viewBox="0 0 14 14" fill="#999"><circle cx="7" cy="4" r="3"/><path d="M1 14c0-4 3-6 6-6s6 2 6 6z"/></svg>Last Name</div>
  <div class="abs field" style="top:3744px;left:201px;width:391px;height:52px">
    <svg width="14" height="14" viewBox="0 0 14 14" fill="#999"><path d="M3 1l2 3-1.5 1.5c.8 2 2.5 3.7 4.5 4.5L9.5 8.5l3 2-1 2.5C6 13 1 8 1 2.5z"/></svg>Email address</div>
  <div class="abs field" style="top:3744px;left:601px;width:390px;height:52px">
    <svg width="16" height="12" viewBox="0 0 16 12" fill="#999"><rect width="16" height="12" rx="1"/><path d="M1 1l7 6 7-6" stroke="#fff" stroke-width="1.3" fill="none"/></svg>Phone</div>
  <div class="abs field msg" style="top:3806px;left:201px;width:790px;height:101px">Message</div>
  <a class="abs send" style="top:3931px;left:499px;width:199px;height:47px">SEND MESSAGE</a>
</section>

<footer>
  <div class="abs brand" style="top:4180px;left:140px;font-size:24px"><span class="brand-mark"></span>CEDAR GROVE</div>
  <div class="abs foot-col" style="top:4084px;left:400px;height:324px"></div>
  <div class="abs foot-col" style="top:4084px;left:601px;height:324px"></div>
  <div class="abs" style="top:4148px;left:855px;width:2px;height:26px;background:var(--teal)"></div>

  <h4 class="abs foot-h serif" style="top:4150px;left:426px">Navigation</h4>
  <ul class="abs foot-links" style="top:4180px;left:430px">
    <li>About Us</li><li>Paster Bio</li><li>Article of Faith</li><li>Listen Live</li><li>Contact Us</li>
  </ul>

  <h4 class="abs foot-h serif" style="top:4150px;left:624px">Donation</h4>
  <p class="abs" style="top:4188px;left:625px;width:210px;font-size:12px;line-height:18px;color:#555">Lorem ipsum dolor sit amet, consectetur adipiscing elit, sed do eiusmod tempor inci</p>
  <a class="abs foot-btn" style="top:4267px;left:622px;width:131px;height:29px;background:var(--green)">Donate Now</a>

  <h4 class="abs foot-h serif" style="top:4152px;left:885px">Contact Us</h4>
  <svg class="abs" style="top:4186px;left:882px" width="34" height="34" viewBox="0 0 34 34"><circle cx="17" cy="17" r="17" fill="var(--green)"/><path d="M17 8a6 6 0 0 0-6 6c0 5 6 11 6 11s6-6 6-11a6 6 0 0 0-6-6z" fill="#fff"/><circle cx="17" cy="14" r="2.2" fill="var(--green)"/></svg>
  <p class="abs" style="top:4185px;left:927px;width:150px;font-size:11px;line-height:17px;color:#444">88 Willow Lane, Suite 210, Fairview, ST 00000 USA</p>
  <a class="abs foot-btn" style="top:4260px;left:882px;width:131px;height:29px;background:var(--teal)">Member Login</a>

  <div class="abs copy">© 2023&nbsp;<span style="text-decoration:underline">Cedar Grove Church</span>. All Rights Reserved</div>
</footer>

</body>
</html>
```